Business Cards

Need business card design that I can update for new employees and details. Needs to incorporate our logo, be bright and fun (in line with tourism and holidays)
Would like a Map of Western Australia on the front with locations all the caravan parks we own (just purchased Tom Price so please include that as well as others listed on our website).
Target Market(s)
Famillies
Contact Information for Business Card
5 Cards -
Neil Perrow (Director) e: perrow@wattlebay.com.au p: 0491 570 156
Mira Perrow (Director) e: perrow@wattlebay.com.au p: 0491 570 157
Owen Halvey (General Manager) e: halvey@wattlebay.com.au p: 0491 570 158
Helen Halvey (General Manager) e: halvey@wattlebay.com.au p: 0491 570 159
Colin Danby (Training and Operations Manager) - e: danby@wattlebay.com.au p:0491 570 110
Colors
Look and feel

```html
<!DOCTYPE html>
<html lang="en">
<head>
<meta charset="utf-8">
<title>Wattlebay Tourist Parks – Business Card</title>
<link href="https://fonts.googleapis.com/css2?family=Roboto:wght@400;500&family=Roboto+Condensed:wght@500;700&display=swap" rel="stylesheet">
<style>
  :root {
    --backdrop: #2b2b2b;
    --card-white: #f3f3f3;
    --teal: #3db8c2;
    --teal-text: #4cbfc7;
    --ink: #4a4a4a;
    --brand-grey: #5a5a5a;
    --rule: #c9c9c9;
    --white: #ffffff;
  }
  * { margin: 0; padding: 0; box-sizing: border-box; }
  html, body { width: 1200px; height: 960px; overflow: hidden; }
  body {
    background: var(--backdrop);
    position: relative;
    font-family: "Roboto", Arial, sans-serif;
  }
  .card {
    position: absolute;
    width: 600px;
    height: 343px;
  }
  .card-front { left: 314px; top: 113px; background: var(--card-white); }
  .card-back  { left: 311px; top: 472px; background: var(--teal); }

  .brand {
    position: absolute;
    text-align: center;
    font-family: "Roboto", Arial, sans-serif;
    font-weight: 400;
    text-transform: uppercase;
    line-height: 1;
  }
  .brand-mark {
    display: block;
    margin: 0 auto 12px;
    width: 70px;
    height: 70px;
  }
  .brand-name { display: block; font-size: 22px; letter-spacing: 4px; }
  .brand-sub  { display: block; font-size: 12px; letter-spacing: 3px; margin-top: 8px; }

  .card-front .brand { left: 40px; top: 116px; width: 246px; color: var(--brand-grey); }
  .card-front .brand-mark { background: var(--teal); }

  .divider {
    position: absolute;
    left: 303px; top: 92px;
    width: 1px; height: 156px;
    background: linear-gradient(to bottom, transparent, var(--rule) 20%, var(--rule) 80%, transparent);
  }

  .contact { position: absolute; left: 334px; top: 110px; }
  .person-name {
    font-family: "Roboto Condensed", Arial, sans-serif;
    font-weight: 700;
    font-size: 22px;
    color: var(--teal-text);
    text-transform: uppercase;
  }
  .person-role {
    font-family: "Roboto Condensed", Arial, sans-serif;
    font-weight: 500;
    font-size: 15px;
    color: var(--teal-text);
    text-transform: uppercase;
    margin: 2px 0 0 2px;
  }
  .details { list-style: none; margin-top: 20px; }
  .details li {
    display: flex;
    align-items: center;
    font-size: 14.5px;
    color: var(--ink);
    height: 19px;
  }
  .details svg { width: 13px; height: 13px; margin-right: 9px; fill: var(--teal); }

  .card-back .brand { left: 0; top: 100px; width: 600px; color: var(--white); }
  .card-back .brand-mark { width: 90px; height: 90px; border: 3px solid var(--white); margin-bottom: 14px; }
  .card-back .brand-name { font-size: 30px; letter-spacing: 5px; }
  .card-back .brand-sub { font-size: 15px; letter-spacing: 4px; margin-top: 10px; }

  .back-url {
    position: absolute;
    left: 0; top: 294px; width: 600px;
    text-align: center;
    color: var(--white);
    font-size: 14px;
    letter-spacing: 2.6px;
  }
</style>
</head>
<body>
  <section class="card card-front">
    <div class="brand">
      <span class="brand-mark"></span>
      <span class="brand-name">Wattlebay</span>
      <span class="brand-sub">Tourist Parks</span>
    </div>
    <div class="divider"></div>
    <div class="contact">
      <h1 class="person-name">Neil Perrow</h1>
      <p class="person-role">Director</p>
      <ul class="details">
        <li>
          <svg viewBox="0 0 16 16"><path d="M3.6 1.2l2.2 2.6c.4.5.3 1.1-.1 1.5l-1 1c.8 1.8 2.2 3.2 4 4l1-1c.4-.4 1-.5 1.5-.1l2.6 2.2c.5.4.5 1.1.1 1.5l-1.2 1.3C11 15.9 8 15 5 12S.1 5 1.9 3.3L3.2 2c.4-.4 1-.4 1.4-.1z"/></svg>
          0491 570 156
        </li>
        <li>
          <svg viewBox="0 0 16 16"><path d="M1 3h14v1.2L8 9 1 4.2z"/><path d="M1 5.6l7 4.8 7-4.8V13H1z"/></svg>
          perrow@wattlebay.com.au
        </li>
        <li>
          <svg viewBox="0 0 16 16"><circle cx="8" cy="8" r="7"/><path d="M1 8h14M8 1c-2.5 2.5-2.5 11.5 0 14M8 1c2.5 2.5 2.5 11.5 0 14" stroke="#f3f3f3" stroke-width="1" fill="none"/></svg>
          www.wattlebay.com.au
        </li>
      </ul>
    </div>
  </section>

  <section class="card card-back">
    <div class="brand">
      <span class="brand-mark"></span>
      <span class="brand-name">Wattlebay</span>
      <span class="brand-sub">Tourist Parks</span>
    </div>
    <p class="back-url">www.wattlebay.com.au</p>
  </section>
</body>
</html>
```